Business Card Design Project

I need a business card designed from scratch. I have an existing logo that I can upload in Illustrator for modification or redesign.

The Company is called Query Lanterns http://querylanterns.com.au and we provide Search Engine Optimization services to Australian businesses. The current logo signifies an increase in visitors, profits etc...

There are no restrictions as to the redesign - colours, style etc are all open to change.

Cards will be full colour and one sided printed at http://www.cardmoxel.com.au so check their requirements for file format and sizes etc.

I will expect all original files upon completion of project.

Target Market(s)

Any business with a web site looking to improve their search engine rankings

Industry/Entity Type

Business

Requirements
Must have
• I like modern, sleek designs. Clean, not fussy, uncluttered.

```html
<!DOCTYPE html>
<html lang="en">
<head>
<meta charset="utf-8">
<title>Query Lanterns – Business Card</title>
<link rel="stylesheet" href="https://fonts.googleapis.com/css2?family=Source+Sans+3:wght@400;700&display=swap">
<style>
  :root {
    --backdrop: #d9dadc;
    --card: #ffffff;
    --brand-blue: #1f6fb8;
    --deep-blue: #1d4f8a;
    --sun-yellow: #f6c52c;
    --amber: #f7ae27;
    --ink: #555557;
    --ink-strong: #4a4a4c;
  }
  * { box-sizing: border-box; margin: 0; padding: 0; }
  html, body {
    width: 1200px; height: 934px; overflow: hidden;
    background: var(--backdrop);
    font-family: "Source Sans 3", "Myriad Pro", sans-serif;
  }
  .canvas { position: relative; width: 1200px; height: 934px; }
  .card {
    position: absolute; top: 66px; width: 472px; height: 828px;
    background: var(--card); border-radius: 26px; overflow: hidden;
    box-shadow: 0 6px 18px rgba(0,0,0,0.18);
  }
  .card--front { left: 74px; }
  .card--back { left: 664px; }

  .brand {
    position: absolute; left: 30px; top: 58px;
    display: flex; align-items: center; gap: 14px;
  }
  .brand__dot { width: 30px; height: 30px; border-radius: 50%; background: var(--sun-yellow); }
  .brand__name {
    font-size: 40px; font-weight: 700; color: var(--brand-blue);
    letter-spacing: -0.5px; line-height: 1;
  }

  .growth-art { position: absolute; }
  .card--front .growth-art {
    left: 0; top: 190px; width: 472px; height: 530px;
    background: linear-gradient(35deg, var(--amber) 0%, var(--sun-yellow) 35%, var(--brand-blue) 70%, var(--deep-blue) 100%);
    opacity: 0.9;
    clip-path: polygon(0 45%, 100% 0, 100% 60%, 0 100%);
  }
  .card--back .growth-art {
    left: 0; top: 40px; width: 460px; height: 570px;
    background: linear-gradient(35deg, var(--amber) 0%, var(--sun-yellow) 35%, var(--brand-blue) 70%, var(--deep-blue) 100%);
    opacity: 0.9;
    clip-path: polygon(0 55%, 100% 0, 100% 55%, 0 100%);
  }

  .address {
    position: absolute; right: 42px; top: 728px;
    text-align: right; font-size: 19px; line-height: 28px; color: var(--ink);
  }

  .holder { position: absolute; left: 44px; top: 52px; color: var(--ink-strong); }
  .holder__name { font-size: 32px; font-weight: 700; line-height: 38px; }
  .holder__role { font-size: 25px; font-weight: 400; line-height: 32px; color: var(--ink); }

  .contact {
    position: absolute; left: 44px; top: 636px;
    list-style: none; font-size: 19px; line-height: 27.5px; color: var(--ink);
  }
  .contact__label { font-weight: 700; color: var(--ink-strong); }
</style>
</head>
<body>
<main class="canvas">
  <section class="card card--front" aria-label="Card front">
    <div class="brand">
      <span class="brand__dot"></span>
      <span class="brand__name">Query Lanterns</span>
    </div>
    <div class="growth-art" role="img" aria-label="Large blue and yellow rising ribbon brand symbol"></div>
    <p class="address">25 Street Name, Road Name,<br>State, Country Code</p>
  </section>

  <section class="card card--back" aria-label="Card back">
    <div class="growth-art" role="img" aria-label="Large blue and yellow rising ribbon brand symbol"></div>
    <div class="holder">
      <p class="holder__name">Name</p>
      <p class="holder__role">Administrator</p>
    </div>
    <ul class="contact">
      <li><span class="contact__label">Phone.</span> 001-555-018274</li>
      <li><span class="contact__label">Fax.</span> 001-555-018274</li>
      <li><span class="contact__label">Cell.</span> 001-555-018274</li>
      <li><span class="contact__label">Email.</span> querylanterns@gmail.com</li>
      <li><span class="contact__label">Web.</span> www.Website.com</li>
    </ul>
  </section>
</main>
</body>
</html>
```